Road Construction Company needs business cards

We would like a new business card designed for our business.

We're a road construction company based in Qld, Australia.

Can the business card please have the following information on it.

Name: Warren Halbeck
Position: General Manager
Phone: 0472 915 348
Email: Warren.halbeck@tovrin.com.au
Address: 87 Marrow Ave, Pendlebay, QLD, 4023
Website: www.tovrin.com.au

Visually we'd like the card to be professional and simple.

Attached is our logo.

Our website is www.tovrin.com.au

Target Market(s)

Men aged 25-60

Contact Information for Business Card

As listed in project description

Font styles to use
Serif

Requirements
Must have
• Large logo on back of card

```html
<!DOCTYPE html>
<html lang="en">
<head>
<meta charset="UTF-8">
<title>Tovrin Road Construction – Business Card</title>
<link href="https://fonts.googleapis.com/css2?family=Montserrat:wght@400;500;700;800&display=swap" rel="stylesheet">
<style>
  :root {
    --page-bg: #e4e4e4;
    --brand-blue: #0b4596;
    --brand-blue-deep: #0a3f8c;
    --brand-blue-light: #1669b4;
    --accent-blue: #2f9bd6;
    --card-white: #f1f1f1;
    --card-white-shade: #e6e6e6;
    --text-grey: #5d5d5d;
    --white: #ffffff;
  }
  * { margin: 0; padding: 0; box-sizing: border-box; }
  html, body {
    width: 1200px; height: 1200px; overflow: hidden;
    background: var(--page-bg);
    font-family: "Montserrat", sans-serif;
  }
  .stage { position: relative; width: 1200px; height: 1200px; }

  .card { position: absolute; left: 234px; width: 731px; height: 418px; overflow: hidden; }

  /* Front */
  .card-front { top: 160px; }
  .front-pattern {
    position: absolute; inset: 0;
    background: linear-gradient(120deg, #5a86bf 0%, var(--brand-blue) 45%, var(--brand-blue-light) 75%, #173f78 100%);
  }
  .front-logo {
    position: absolute; left: 0; right: 0; top: 176px;
    text-align: center; color: var(--white);
  }

  /* Back */
  .card-back {
    top: 632px;
    background: linear-gradient(110deg, var(--card-white-shade) 0%, var(--card-white) 60%, #f5f5f5 100%);
  }
  .back-logo {
    position: absolute; left: 0; right: 0; top: 70px;
    text-align: center; color: var(--brand-blue);
  }
  .back-logo .logo-tagline { color: var(--accent-blue); }

  .logo-name {
    display: block;
    font-weight: 800; font-size: 48px; line-height: 1;
    letter-spacing: 1px;
  }
  .logo-tagline {
    display: block; margin-top: 8px;
    font-weight: 700; font-size: 11px; letter-spacing: 8.4px;
    padding-left: 8px;
  }

  .person {
    position: absolute; right: 436px; top: 230px; text-align: right;
  }
  .person-name {
    font-weight: 700; font-size: 31px; color: var(--brand-blue-deep); line-height: 1.1;
  }
  .person-role {
    margin-top: 6px; font-size: 18.5px; color: var(--text-grey); font-weight: 500;
  }
  .divider {
    position: absolute; left: 338px; top: 220px; width: 2px; height: 67px;
    background: var(--accent-blue);
  }
  .contacts {
    position: absolute; left: 374px; top: 212px; list-style: none;
  }
  .contacts li {
    display: flex; align-items: center; height: 28px;
    font-size: 19px; color: var(--text-grey); font-weight: 500;
  }
  .contacts svg { width: 17px; height: 17px; margin-right: 10px; fill: var(--brand-blue); flex: none; }

  .address-band {
    position: absolute; left: 0; right: 0; bottom: 0; height: 52px;
    background: var(--brand-blue);
    color: var(--white); font-size: 18px; font-weight: 500;
    display: flex; align-items: center; justify-content: center;
  }
</style>
</head>
<body>
<main class="stage">
  <section class="card card-front">
    <div class="front-pattern" role="img" aria-label="Repeating pattern of embossed upward chevrons on blue"></div>
    <div class="front-logo">
      <span class="logo-name">TOVRIN</span>
      <span class="logo-tagline">ROAD CONSTRUCTION</span>
    </div>
  </section>

  <section class="card card-back">
    <div class="back-logo">
      <span class="logo-name">TOVRIN</span>
      <span class="logo-tagline">ROAD CONSTRUCTION</span>
    </div>

    <div class="person">
      <div class="person-name">Warren Halbeck</div>
      <div class="person-role">General Manager</div>
    </div>

    <div class="divider"></div>

    <ul class="contacts">
      <li>
        <svg viewBox="0 0 24 24" aria-hidden="true"><path d="M6.6 10.8a15.1 15.1 0 0 0 6.6 6.6l2.2-2.2a1 1 0 0 1 1-.25 11.4 11.4 0 0 0 3.6.57 1 1 0 0 1 1 1V20a1 1 0 0 1-1 1A17 17 0 0 1 3 4a1 1 0 0 1 1-1h3.5a1 1 0 0 1 1 1c0 1.25.2 2.45.57 3.57a1 1 0 0 1-.25 1z"/></svg>
        0472 915 348
      </li>
      <li>
        <svg viewBox="0 0 24 24" aria-hidden="true"><path d="M2 5h20v14H2z M3.5 6.5 12 12.5l8.5-6" fill="none" stroke="currentColor"/><path d="M2 5h20v14H2V5zm2 2v.3l8 5.4 8-5.4V7H4z"/></svg>
        Warren.halbeck@tovrin.com.au
      </li>
      <li>
        <svg viewBox="0 0 24 24" aria-hidden="true"><path d="M12 2a10 10 0 1 0 0 20 10 10 0 0 0 0-20zm6.9 9h-3a15.5 15.5 0 0 0-1.3-6.1A8 8 0 0 1 18.9 11zM12 4.1c.9 1.3 1.8 3.6 1.9 6.9h-3.8c.1-3.3 1-5.6 1.9-6.9zM9.4 4.9A15.5 15.5 0 0 0 8.1 11h-3a8 8 0 0 1 4.3-6.1zM5.1 13h3a15.5 15.5 0 0 0 1.3 6.1A8 8 0 0 1 5.1 13zm6.9 6.9c-.9-1.3-1.8-3.6-1.9-6.9h3.8c-.1 3.3-1 5.6-1.9 6.9zm2.6-.8a15.5 15.5 0 0 0 1.3-6.1h3a8 8 0 0 1-4.3 6.1z"/></svg>
        www.tovrin.com.au
      </li>
    </ul>

    <div class="address-band">87 Marrow Ave, Pendlebay, QLD, 4023</div>
  </section>
</main>
</body>
</html>
```